Every Shelf Set Neatly or ESN Organized needs a business card design. ESN Organized is a professi

We need a business card design that is clean, sharp and conveys a sense of organization. I already have a logo.

Target Market(s)

Families (specifically mothers), small business owners, parents, seniors

Industry/Entity Type

Business

Contact Information for Business Card

My website is www.esnorganized-example.com and my Facebook page is http://www.sociallink-example.com/everyshelfsetneatly. The phone number is 418-552-7094 and I want to be listed as Lorna M. Pelham, Owner

Requirements
Must have
• My logo.

```html
<!DOCTYPE html>
<html lang="en">
<head>
<meta charset="utf-8">
<title>ESN Organized – Business Card</title>
<link rel="stylesheet" href="https://fonts.googleapis.com/css2?family=Montserrat:wght@300;400&family=Open+Sans:ital,wght@0,400;0,600;1,700&display=swap">
<style>
  :root {
    --stage: #000000;
    --card: #323337;
    --brand-blue: #1a7fd8;
    --text-light: #f2f2f2;
    --divider: #45464b;
  }
  * { margin: 0; padding: 0; box-sizing: border-box; }
  html, body {
    width: 1200px; height: 900px; overflow: hidden;
    background: var(--stage);
  }
  .canvas { position: relative; width: 1200px; height: 900px; }
  .card {
    position: absolute; top: 271px;
    width: 457px; height: 281px;
    background: var(--card);
    border-radius: 14px;
    overflow: hidden;
  }
  .card--front { left: 137px; }
  .card--back { left: 626px; }

  .brand-name {
    font-family: "Montserrat", sans-serif;
    font-weight: 300;
    color: var(--brand-blue);
    line-height: 1;
  }
  .card--front .brand-name {
    position: absolute; left: 30px; top: 92px;
    font-size: 88px; letter-spacing: 2px;
  }
  .divider {
    position: absolute; left: 225px; top: 72px;
    width: 1px; height: 128px;
    background: var(--divider);
  }
  .contact {
    position: absolute; left: 254px; top: 79px;
    font-family: "Open Sans", sans-serif;
    color: var(--text-light);
  }
  .contact__name {
    font-weight: 600; font-size: 16.5px;
    color: var(--brand-blue); line-height: 20px;
  }
  .contact__role { font-size: 12.5px; line-height: 16px; }
  .contact__list { list-style: none; margin-top: 18px; }
  .contact__item {
    display: flex; align-items: center;
    font-size: 12.5px; line-height: 19px;
  }
  .contact__icon { width: 9px; height: 9px; margin-right: 6px; fill: var(--brand-blue); }
  .social-bar {
    position: absolute; left: 0; right: 0; top: 243px;
    display: flex; align-items: center; gap: 8px;
  }
  .social-bar__rule { height: 1.5px; background: var(--brand-blue); }
  .social-bar__rule--left { width: 95px; }
  .social-bar__rule--right { flex: 1; }
  .social-bar__link {
    font-family: "Open Sans", sans-serif;
    font-style: italic; font-weight: 700;
    font-size: 12px; color: var(--brand-blue);
    white-space: nowrap;
  }

  .card--back { text-align: center; }
  .card--back .brand-name {
    position: absolute; left: 0; right: 0; top: 80px;
    font-size: 58px; letter-spacing: 1px;
  }
  .tagline {
    position: absolute; left: 0; right: 0; top: 149px;
    font-family: "Montserrat", sans-serif;
    color: var(--text-light);
  }
  .tagline__top { font-size: 20px; letter-spacing: 3px; line-height: 24px; }
  .tagline__main { font-size: 29px; letter-spacing: 7px; line-height: 34px; }
</style>
</head>
<body>
<main class="canvas">
  <section class="card card--front" aria-label="Business card front">
    <div class="brand-name">ESN</div>
    <div class="divider"></div>
    <div class="contact">
      <p class="contact__name">Lorna M. Pelham</p>
      <p class="contact__role">Owner</p>
      <ul class="contact__list">
        <li class="contact__item">
          <svg class="contact__icon" viewBox="0 0 10 10"><path d="M2 0.5 L3.6 2.6 L2.7 3.6 Q3.6 5.8 6.4 7.3 L7.4 6.4 L9.5 8 L8.3 9.5 Q1.5 8.3 0.5 1.7 Z"/></svg>
          418-552-7094
        </li>
        <li class="contact__item">
          <svg class="contact__icon" viewBox="0 0 10 10"><path d="M0 2 H10 V8.5 H0 Z M0.8 2.6 L5 5.6 L9.2 2.6" stroke="#323337" stroke-width="0.9"/></svg>
          info@esnorganized-example.com
        </li>
        <li class="contact__item">
          <svg class="contact__icon" viewBox="0 0 10 10"><circle cx="5" cy="5" r="4.7"/><path d="M0.5 5 H9.5 M5 0.5 Q2.5 5 5 9.5 Q7.5 5 5 0.5" fill="none" stroke="#323337" stroke-width="0.8"/></svg>
          www.esnorganized-example.com
        </li>
      </ul>
    </div>
    <div class="social-bar">
      <span class="social-bar__rule social-bar__rule--left"></span>
      <span class="social-bar__link">www.sociallink-example.com/everyshelfsetneatly</span>
      <span class="social-bar__rule social-bar__rule--right"></span>
    </div>
  </section>

  <section class="card card--back" aria-label="Business card back">
    <div class="brand-name">ESN</div>
    <div class="tagline">
      <p class="tagline__top">Every Shelf Set</p>
      <p class="tagline__main">NEATLY</p>
    </div>
  </section>
</main>
</body>
</html>
```